Business Card for Vorla Parts Wholesale supplier

Hi There! I need a new business card for our company. We are specialized in selling Vorla parts, mostly we sell new LCD screens for Zelnar and Drelks. I would like to see that back in the design.

You can find the colors and logo's on our website: www.hartuvo.nl

Industry/Entity Type

Business

Contact Information for Business Card

My Details:
Tobias Lindqvist

Phone: 0031687203316
E-mail: Tobias@hartuvo.nl

Slogan: "Because Quality Matters"

Font styles to use
Sans Serif

Colors

Designer to choose colors to be used in the design.

Requirements
Must have
• A Black backside with the Hartuvo logo on it. The front side should be clean with only my contact details.
• But I'm also open for something really different or awesome!
Nice to have
• Remember that we are in the parts & repairing industry, So i'll be handing those business cards mainly to repair companies. Maybe you can do something with that thought :)

```html
<!DOCTYPE html>
<html lang="en">
<head>
<meta charset="utf-8">
<title>Hartuvo business card</title>
<link href="https://fonts.googleapis.com/css2?family=Roboto:wght@400;500;700&display=swap" rel="stylesheet">
<style>
  :root {
    --page: #e4e4e4;
    --card: #151617;
    --card-soft: #2a2b2d;
    --orange: #e8671c;
    --white: #f4f4f4;
    --muted: #c9c9c9;
    --grey-band: #8c8d8f;
  }
  * { margin: 0; padding: 0; box-sizing: border-box; }
  html, body {
    width: 1200px; height: 576px; overflow: hidden;
    background: var(--page);
    font-family: "Roboto", Arial, sans-serif;
  }
  .stage { position: relative; width: 1200px; height: 576px; }

  .card {
    position: absolute; top: 138px;
    width: 482px; height: 293px;
    border-radius: 13px; overflow: hidden;
    background: var(--card);
    box-shadow: 0 4px 10px rgba(0,0,0,.25);
  }
  .card--back { left: 82px; }
  .card--front { left: 602px; }

  .back-photo {
    position: absolute; inset: 0;
    background:
      radial-gradient(ellipse 70% 55% at 70% 20%, #3a3b3d 0%, #26272a 45%, transparent 80%),
      linear-gradient(160deg, #1d1e20 0%, #2b2c2e 60%, #252628 100%);
  }

  .brand { position: absolute; display: flex; align-items: center; }
  .brand__dot {
    border-radius: 50%; background: var(--orange); flex: none;
  }
  .brand__name {
    color: var(--white); font-weight: 700; letter-spacing: -0.5px; line-height: 1;
  }
  .card--back .brand { left: 50%; top: 144px; transform: translateX(-50%); gap: 14px; }
  .card--back .brand__dot { width: 48px; height: 48px; }
  .card--back .brand__name { font-size: 50px; }

  .card--front .brand { left: 28px; top: 50px; gap: 16px; }
  .card--front .brand__dot { width: 54px; height: 54px; }
  .card--front .brand__name { font-size: 56px; }

  .person { position: absolute; left: 31px; top: 196px; }
  .person__name { color: var(--white); font-size: 18px; font-weight: 500; }
  .person__role { color: var(--muted); font-size: 11px; margin-top: 5px; }

  .contacts {
    position: absolute; left: 281px; top: 178px;
    list-style: none; display: flex; flex-direction: column; gap: 4px;
  }
  .contacts li {
    display: flex; align-items: center; gap: 12px;
    color: var(--white); font-size: 12px; height: 13px;
  }
  .contacts svg { width: 11px; height: 11px; fill: var(--orange); flex: none; }

  .band-grey {
    position: absolute; left: 0; bottom: 0; width: 240px; height: 19px;
    background: var(--grey-band);
  }
  .band-orange {
    position: absolute; right: 0; bottom: 0; width: 272px; height: 38px;
    background: var(--orange);
    clip-path: polygon(24px 0, 100% 0, 100% 100%, 0 100%);
    display: flex; align-items: center; justify-content: center;
    padding-left: 40px;
  }
  .slogan { color: var(--white); font-size: 12.5px; }
</style>
</head>
<body>
<main class="stage">
  <section class="card card--back" aria-label="Card back">
    <div class="back-photo" role="img" aria-label="Dark close-up photo of a phone with a cracked screen"></div>
    <div class="brand">
      <span class="brand__dot"></span>
      <span class="brand__name">hartuvo</span>
    </div>
  </section>

  <section class="card card--front" aria-label="Card front">
    <div class="brand">
      <span class="brand__dot"></span>
      <span class="brand__name">hartuvo</span>
    </div>

    <div class="person">
      <p class="person__name">Tobias Lindqvist</p>
      <p class="person__role">Managing Director</p>
    </div>

    <ul class="contacts">
      <li>
        <svg viewBox="0 0 24 24" aria-hidden="true"><path d="M6.6 10.8a15.1 15.1 0 0 0 6.6 6.6l2.2-2.2c.3-.3.7-.4 1-.2 1.1.4 2.3.6 3.6.6.6 0 1 .4 1 1V20c0 .6-.4 1-1 1A17 17 0 0 1 3 4c0-.6.4-1 1-1h3.5c.6 0 1 .4 1 1 0 1.3.2 2.5.6 3.6.1.3 0 .7-.2 1z"/></svg>
        0031687203316
      </li>
      <li>
        <svg viewBox="0 0 24 24" aria-hidden="true"><path d="M2 5h20v14H2z M3.5 6.5 12 13l8.5-6.5" fill="none" stroke="#e8671c" stroke-width="2"/></svg>
        Tobias@hartuvo.nl
      </li>
      <li>
        <svg viewBox="0 0 24 24" aria-hidden="true"><g fill="none" stroke="#e8671c" stroke-width="2"><circle cx="12" cy="12" r="9.5"/><ellipse cx="12" cy="12" rx="4" ry="9.5"/><path d="M2.5 12h19"/></g></svg>
        www.hartuvo.nl
      </li>
    </ul>

    <div class="band-grey"></div>
    <div class="band-orange"><span class="slogan">Because Quality Matters</span></div>
  </section>
</main>
</body>
</html>
```